Kentucky residential recovery center needs a flyer design

We need a flyer design for a 16 bed male residential/inpatient recovery center based in Richmond, Kentucky. The facility provides short term (average 30 day) treatment to those struggling with substace abuse and addiction. The design should communicate trust, assurance, safety.
Our wesite provides more information https://corvalmend.org/treatment-services/residential-treatment/

Target Market(s)

Men (typically 30-50) struggling with substance addiction

```html
<!DOCTYPE html>
<html lang="en">
<head>
<meta charset="utf-8">
<title>Corvalmend Residential Recovery Flyer</title>
<link href="https://fonts.googleapis.com/css2?family=Montserrat:ital,wght@0,500;0,600;0,700;1,800;1,900&family=Lato:wght@400&display=swap" rel="stylesheet">
<style>
  :root {
    --backdrop: #d0d0d0;
    --paper: #f1f1f3;
    --navy: #1f2558;
    --sky: #6cb4e6;
    --pink: #e8457f;
    --white: #ffffff;
  }
  * { margin: 0; padding: 0; box-sizing: border-box; }
  html, body { width: 1200px; height: 1200px; overflow: hidden; background: var(--backdrop); }
  .flyer {
    position: absolute; left: 207px; top: 45px; width: 806px; height: 1108px;
    background: var(--paper); overflow: hidden;
    font-family: "Lato", sans-serif;
  }
  .hero {
    position: absolute; left: 0; top: 0; width: 806px; height: 427px;
    background: linear-gradient(160deg, #cfc7bb 0%, #8f8170 35%, #3b3733 60%, #5a5f88 85%, #8a4a4a 100%);
  }
  .brand {
    position: absolute; left: 42px; top: 38px; width: 132px; height: 132px; border-radius: 50%;
    background: var(--white); display: flex; align-items: center; justify-content: center;
    font-family: "Montserrat", sans-serif; font-weight: 700; font-size: 17px; color: var(--navy);
  }
  .headline {
    position: absolute; left: 44px; top: 282px; width: 750px;
    font-family: "Montserrat", sans-serif; font-weight: 900; font-style: italic;
    font-size: 42.5px; line-height: 38.5px; color: var(--white); text-transform: uppercase;
    letter-spacing: -0.5px;
  }
  .stats {
    position: absolute; left: 0; top: 427px; width: 806px; height: 187px; background: var(--sky);
  }
  .stat-divider { position: absolute; top: 34px; width: 4px; height: 116px; background: var(--white); }
  .stat {
    position: absolute; top: 0; height: 187px; width: 200px; color: var(--white); text-align: center;
  }
  .stat-value {
    font-family: "Montserrat", sans-serif; font-weight: 900; font-style: italic; font-size: 31px; line-height: 32px;
  }
  .stat-label {
    font-family: "Montserrat", sans-serif; font-weight: 800; font-style: italic; font-size: 11.5px; line-height: 16px;
    text-transform: uppercase; margin-top: 5px;
  }
  .stat-note { font-size: 8.5px; line-height: 11px; margin-top: 14px; text-align: left; padding: 0 10px; }
  .services-heading {
    position: absolute; left: 26px; top: 639px;
    font-family: "Montserrat", sans-serif; font-weight: 500; font-size: 14.5px; color: var(--navy); letter-spacing: 0.2px;
  }
  .heading-mark { position: absolute; left: 0; top: 635px; width: 19px; height: 24px; background: var(--pink); }
  .service-list { position: absolute; left: 48px; top: 684px; list-style: none; }
  .service-list li {
    position: relative; padding-left: 28px; height: 23.7px; line-height: 23.7px;
    font-family: "Montserrat", sans-serif; font-weight: 600; font-size: 14px; font-variant: small-caps;
    letter-spacing: 1.5px; color: var(--navy);
  }
  .service-list li::before {
    content: ""; position: absolute; left: 0; top: 5px; width: 14px; height: 14px; background: var(--navy);
  }
  .service-list li:nth-child(even)::before { background: var(--sky); }
  .photo { position: absolute; }
  .photo-main { left: 443px; top: 614px; width: 363px; height: 272px;
    background: linear-gradient(150deg, #e8e2d8 0%, #a89478 45%, #6f6a5a 70%, #8a7358 100%); }
  .photo-bunks { left: 423px; top: 886px; width: 120px; height: 117px;
    background: linear-gradient(160deg, #d9d4cc 0%, #8c7c68 60%, #5a4c3e 100%); }
  .photo-lounge { left: 543px; top: 886px; width: 128px; height: 100px;
    background: linear-gradient(160deg, #c9bfae 0%, #4a4540 55%, #6a6f90 100%); }
  .photo-sofa { left: 671px; top: 886px; width: 135px; height: 100px;
    background: linear-gradient(160deg, #d8d0c4 0%, #5a4e44 55%, #7a6a80 100%); }
  .accent { position: absolute; }
  .accent-bar-left { left: 434px; top: 687px; width: 9px; height: 199px; background: var(--sky); }
  .accent-pink-left { left: 423px; top: 870px; width: 20px; height: 16px; background: var(--pink); }
  .accent-bar-bottom { left: 543px; top: 986px; width: 231px; height: 7px; background: var(--sky); }
  .accent-pink-bottom { left: 786px; top: 986px; width: 20px; height: 17px; background: var(--pink); }
  .contact { position: absolute; color: var(--navy); }
  .contact-icon { position: absolute; }
  .contact-email { left: 88px; top: 1033px; font-size: 9.5px; }
  .contact-phone { left: 316px; top: 1029px; font-size: 14px; }
  .contact-address { left: 517px; top: 1025px; font-size: 9px; line-height: 12px; }
  .contact-address p + p { margin-top: 8px; }
</style>
</head>
<body>
<main class="flyer">
  <div class="hero" role="img" aria-label="Photo of the residence lounge with a leather sofa, coffee table and patterned rug"></div>
  <div class="brand">Corvalmend</div>
  <h1 class="headline">Kentuckys leading drug &amp;<br>alcohol addiction<br>treatment</h1>

  <section class="stats">
    <div class="stat" style="left:13px; padding-top:28px;">
      <div class="stat-value">#1</div>
      <div class="stat-label">Best drug &amp;<br>alcohol rehab center</div>
      <div class="stat-note" style="margin-top:16px;">Voted one of the best Alcohol and Drug rehab centers</div>
    </div>
    <div class="stat-divider" style="left:221px;"></div>
    <div class="stat" style="left:225px; padding-top:42px;">
      <div class="stat-value">2,500+</div>
      <div class="stat-label">Patients treated</div>
      <div class="stat-note" style="margin-top:14px;">Over 2,500 patients treated successfully and counting</div>
    </div>
    <div class="stat-divider" style="left:435px;"></div>
    <div class="stat" style="left:431px; padding-top:42px;">
      <div class="stat-value">100+</div>
      <div class="stat-label">Years</div>
      <div class="stat-note" style="margin-top:14px; text-align:center;">Over 100 years of medical and clinical experience behind our team</div>
    </div>
    <div class="stat-divider" style="left:620px;"></div>
    <div class="stat" style="left:618px; padding-top:42px;">
      <div class="stat-value">95%</div>
      <div class="stat-label" style="line-height:19px;">Satisfaction<br>rating</div>
      <div class="stat-note" style="margin-top:7px; text-align:center;">Our patients rate us 95 out of 100</div>
    </div>
  </section>

  <div class="heading-mark"></div>
  <h2 class="services-heading">BELOW IS A SUMMARY OF SERVICES OFFERED BY US:</h2>
  <ul class="service-list">
    <li>Outpatient</li>
    <li>Inpatient/Residential</li>
    <li>Intensive Outpatient</li>
    <li>Targeted Case Management</li>
    <li>Peer Support</li>
    <li>Individual and Group Therapy</li>
    <li>Medicated Assisted Treatment</li>
    <li>(‘MAT’)</li>
    <li>Novabrin, Buprenorphine &amp; Veltrina</li>
    <li>Treatment</li>
    <li>Physician Appointments</li>
    <li>Telemedicine</li>
  </ul>

  <div class="accent accent-bar-left"></div>
  <div class="photo photo-main" role="img" aria-label="Photo of a resident bedroom with a sofa and bunk beds"></div>
  <div class="accent accent-pink-left"></div>
  <div class="photo photo-bunks" role="img" aria-label="Photo of a bedroom with bunk beds and a table"></div>
  <div class="photo photo-lounge" role="img" aria-label="Photo of the lounge with leather sofas and a television"></div>
  <div class="photo photo-sofa" role="img" aria-label="Photo of a living area with a leather sofa and artwork"></div>
  <div class="accent accent-bar-bottom"></div>
  <div class="accent accent-pink-bottom"></div>

  <svg class="contact-icon" style="left:47px; top:1026px;" width="27" height="27" viewBox="0 0 24 24" aria-hidden="true">
    <circle cx="12" cy="12" r="4" fill="none" stroke="#6cb4e6" stroke-width="2.4"/>
    <path d="M16 8v5.5a2.5 2.5 0 0 0 5 0V12a9 9 0 1 0-3.5 7.1" fill="none" stroke="#6cb4e6" stroke-width="2.4" stroke-linecap="round"/>
  </svg>
  <div class="contact contact-email">ADMISSIONS@CORVALMEND.ORG</div>

  <svg class="contact-icon" style="left:289px; top:1026px;" width="25" height="25" viewBox="0 0 24 24" aria-hidden="true">
    <path d="M6.6 10.8a15.1 15.1 0 0 0 6.6 6.6l2.2-2.2a1 1 0 0 1 1-.25 11.4 11.4 0 0 0 3.6.57 1 1 0 0 1 1 1V20a1 1 0 0 1-1 1A17 17 0 0 1 3 4a1 1 0 0 1 1-1h3.5a1 1 0 0 1 1 1c0 1.25.2 2.45.57 3.57a1 1 0 0 1-.25 1z" fill="#6cb4e6"/>
  </svg>
  <div class="contact contact-phone">859-555-0142</div>

  <svg class="contact-icon" style="left:482px; top:1026px;" width="18" height="25" viewBox="0 0 18 25" aria-hidden="true">
    <path d="M9 0a9 9 0 0 0-9 9c0 6.5 9 16 9 16s9-9.5 9-16a9 9 0 0 0-9-9z" fill="#6cb4e6"/>
    <circle cx="9" cy="9" r="3.5" fill="#f1f1f3"/>
  </svg>
  <div class="contact contact-address">
    <p>ADDRESS (CENTRAL KY CLINIC)<br>410 &amp; 412 Maplecrest Drive, Richmond, Kentucky 40475</p>
    <p>ADDRESS (NORTHERN KY CLINIC)<br>2870 Oakridge Court, Burlington, Kentucky 41005</p>
  </div>
</main>
</body>
</html>
```